RW Framewell Inc Business cards

We need business cards using our existing logo but slightly modified. Right now the logo says RW Loadbearing Masonry. We want to keep the RW part of the design, but replace the Structural Concrete portion with "FRAMEWELL". Please see the attached file.
Ideally this would be a blank template so we can add Different Names, titles, and phone numbers later.
On the one side we want only the logo and on the other side the detail. I'm attaching an example for you to see.
Please reach out with any other questions. Our address and other details will be given out once we find a design we like.

Target Market(s)

Construction Industry

```html
<!DOCTYPE html>
<html lang="en">
<head>
<meta charset="utf-8">
<title>RW Framewell Inc – Business Cards</title>
<link href="https://fonts.googleapis.com/css2?family=Montserrat:wght@300;700&family=Raleway:wght@300;400&display=swap" rel="stylesheet">
<style>
  :root {
    --brand-blue: #0077c8;
    --ink-grey: #555a60;
    --rule-grey: #4a4a4a;
    --paper: #f2f2f2;
    --stage: #dcdcdc;
  }
  * { box-sizing: border-box; margin: 0; padding: 0; }
  html, body { width: 1200px; height: 900px; overflow: hidden; }
  body {
    background: var(--stage);
    display: flex;
    flex-direction: column;
    align-items: center;
    justify-content: center;
    gap: 40px;
    font-family: "Raleway", sans-serif;
  }
  .card {
    width: 700px;
    height: 400px;
    position: relative;
  }
  .card--back {
    background: var(--brand-blue);
    display: flex;
    align-items: center;
    justify-content: center;
  }
  .card--front { background: var(--paper); }

  .wordmark {
    font-family: "Montserrat", sans-serif;
    font-weight: 700;
    text-align: center;
    line-height: 1;
  }
  .wordmark__initials { display: block; font-size: 96px; letter-spacing: 2px; }
  .wordmark__name { display: block; font-size: 22px; letter-spacing: 14px; margin-top: 14px; margin-right: -14px; }
  .card--back .wordmark { color: #ffffff; }
  .card--front .wordmark {
    color: var(--brand-blue);
    position: absolute;
    top: 48px;
    right: 40px;
  }
  .card--front .wordmark__initials { font-size: 76px; }
  .card--front .wordmark__name { font-size: 17px; letter-spacing: 11px; margin-right: -11px; margin-top: 10px; }

  .details {
    position: absolute;
    left: 40px;
    bottom: 36px;
  }
  .details__name {
    font-family: "Montserrat", sans-serif;
    font-weight: 700;
    font-size: 27px;
    color: var(--brand-blue);
    letter-spacing: 0.3px;
  }
  .details__title {
    font-weight: 400;
    font-size: 16px;
    color: var(--ink-grey);
    margin-top: 4px;
  }
  .details__rule {
    width: 18px;
    height: 2px;
    background: var(--rule-grey);
    margin: 12px 0 14px;
  }
  .contact { list-style: none; }
  .contact__item {
    display: flex;
    align-items: center;
    gap: 12px;
    font-weight: 300;
    font-size: 17px;
    color: var(--ink-grey);
    height: 27px;
  }
  .contact__icon { width: 16px; height: 16px; flex: none; }
</style>
</head>
<body>

  <section class="card card--back" aria-label="Card back">
    <div class="wordmark">
      <span class="wordmark__initials">RW</span>
      <span class="wordmark__name">FRAMEWELL</span>
    </div>
  </section>

  <section class="card card--front" aria-label="Card front">
    <div class="wordmark">
      <span class="wordmark__initials">RW</span>
      <span class="wordmark__name">FRAMEWELL</span>
    </div>

    <div class="details">
      <h1 class="details__name">DANA MERCER</h1>
      <p class="details__title">FOUNDER</p>
      <div class="details__rule"></div>
      <ul class="contact">
        <li class="contact__item">
          <svg class="contact__icon" viewBox="0 0 16 16" aria-hidden="true">
            <path d="M3.5 1.5 L6 4.5 L4.6 6.2 C5.4 8 7.9 10.6 9.8 11.4 L11.5 10 L14.5 12.5 L12.8 14.5 C8 14.5 1.5 8 1.5 3.2 Z" fill="var(--brand-blue)"/>
            <path d="M9.5 2.5 A4 4 0 0 1 13.5 6.5 M9.5 0.8 A5.7 5.7 0 0 1 15.2 6.5" stroke="var(--brand-blue)" stroke-width="1.2" fill="none"/>
          </svg>
          <span>+000000000000</span>
        </li>
        <li class="contact__item">
          <svg class="contact__icon" viewBox="0 0 16 16" aria-hidden="true">
            <rect x="0.5" y="3" width="15" height="10" fill="var(--brand-blue)"/>
            <path d="M0.5 3 L8 9 L15.5 3 M0.5 13 L6 8 M15.5 13 L10 8" stroke="#fff" stroke-width="1.2" fill="none"/>
          </svg>
          <span>INFO@YOURMAIL.COM</span>
        </li>
        <li class="contact__item">
          <svg class="contact__icon" viewBox="0 0 16 16" aria-hidden="true">
            <circle cx="8" cy="8" r="7" fill="none" stroke="var(--brand-blue)" stroke-width="1.4"/>
            <ellipse cx="8" cy="8" rx="3" ry="7" fill="none" stroke="var(--brand-blue)" stroke-width="1.1"/>
            <path d="M1 8 H15" stroke="var(--brand-blue)" stroke-width="1.1"/>
          </svg>
          <span>WWW.YOURWEBSITE.COM</span>
        </li>
      </ul>
    </div>
  </section>

</body>
</html>
```